Lantern Petals Website v.1 - attract floral shop franchisees

I need a simple information website for my new business. We are a franchisor of flower shops. The overall purpose of the website is to promote the company and the service, especially to potential franchisees and retailers. Only about 4 pages are required including homepage, About, For Supermarkets, For Franchisees, and Contact. No special functions are required except the site will have two separate inquiry forms that must be filled out online and submitted via automated email. Similarly, an email form should be linked from the Contact page. I have a logo and business cards designed by ArtMingle, and I would like the site to have a consistent color scheme and style. The key to design will be to express the joy and love associated with flowers and floral bouquets.
IMPORTANT - I will be exporting the website design to Wordpress CMS in a site hosted by HostNimbus. For smooth integration into WordPress hosted by HostNimbus, the designer should build the site using a WordPress-friendly format. Ideally, they should use HTML, CSS, and PHP. Creating a custom theme or using a page builder that exports to WordPress-compatible files is best. This ensures the site can be easily imported and managed within WordPress.

Target Market(s)

Potential franchisees (existing florists or creative types who might like to own a floral business) and supermarkets who might want us to run their floral department

Industry/Entity Type

Floral retailing

Requirements
Must have
• A brand theme that is beautiful, consistent throughout and builds on the logo design
Nice to have
• Show gender and ethnic diversity in customers and florists. Pictures of happy florists (for franchisees) and pictures of amazing floral department displays (for supermarkets)

```html
<!DOCTYPE html>
<html lang="en">
<head>
<meta charset="UTF-8">
<title>Lantern Petals — Fresh Flowers Franchise</title>
<link href="https://fonts.googleapis.com/css2?family=Libre+Baskerville:wght@400;700&family=Poppins:wght@400;500&display=swap" rel="stylesheet">
<style>
:root{
  --orange:#e07b39;
  --green:#11793d;
  --ink:#1d1d1d;
  --body:#3a3a3a;
  --muted:#8a8a8a;
  --panel:#eef0f2;
  --line:#cfd3d6;
  --white:#ffffff;
}
*{margin:0;padding:0;box-sizing:border-box}
html,body{width:1200px;height:3405px;overflow:hidden}
body{position:relative;background:var(--white);font-family:'Poppins',sans-serif;color:var(--body)}
.abs{position:absolute}
.serif{font-family:'Libre Baskerville',serif}
.btn{position:absolute;background:var(--orange);color:var(--white);font-size:12px;font-weight:500;display:flex;align-items:center;justify-content:center;border-radius:4px}
.center{left:0;width:1200px;text-align:center}
.eyebrow{font-size:11px;color:var(--orange);letter-spacing:.3px;text-transform:uppercase}

/* header */
.brand{display:flex;align-items:center;gap:8px;font-family:'Libre Baskerville',serif;font-size:19px;color:var(--orange)}
.brand-dot{width:22px;height:22px;border-radius:50%;background:var(--orange)}
.nav a{position:absolute;top:52px;font-size:12px;color:#444;text-decoration:none;display:flex;align-items:center;gap:10px}
.nav a.active{color:var(--orange)}

/* hero */
.hero{left:0;top:110px;width:1200px;height:432px;
  background:
    radial-gradient(ellipse 260px 200px at 90px 80px,#e58aa3 0%,rgba(229,138,163,0) 100%),
    radial-gradient(ellipse 300px 240px at 1110px 180px,#eef0e6 0%,rgba(238,240,230,0) 100%),
    radial-gradient(ellipse 200px 160px at 1050px 60px,#d9637a 0%,rgba(217,99,122,0) 100%),
    radial-gradient(ellipse 180px 140px at 230px 300px,#8fbfae 0%,rgba(143,191,174,0) 100%),
    linear-gradient(90deg,#cfcac4 0%,#d8d2cb 30%,#ddd6ce 70%,#cfd4c6 100%)}
.hero-paper{left:368px;top:160px;width:506px;height:382px;background:linear-gradient(180deg,#e8d3b3,#dcc19c);border-radius:2px}

/* cards */
.card{position:absolute;top:718px;width:260px;height:218px;background:var(--white);box-shadow:0 10px 40px rgba(0,0,0,.08);text-align:center}
.card svg{margin-top:24px}
.card h3{font-family:'Libre Baskerville',serif;font-size:14px;color:var(--ink);margin-top:8px;letter-spacing:.3px}
.card p{font-size:11.5px;line-height:22px;color:#444;margin:10px 24px 0}

.para{font-size:11.5px;line-height:22.2px;color:#333}
.photo{position:absolute}

/* form */
.lbl{position:absolute;font-family:'Libre Baskerville',serif;font-size:9.5px;color:#555}
.field{position:absolute;border:1px solid var(--line);background:var(--white)}
.contact-line{position:absolute;left:640px;display:flex;align-items:flex-start;gap:14px;font-family:'Libre Baskerville',serif;font-size:12px;font-weight:700;color:var(--ink)}

/* footer */
.footer{left:0;top:3157px;width:1200px;height:248px;background:var(--green)}
.social{position:absolute;top:3303px;width:28px;height:28px;border-radius:50%;background:rgba(255,255,255,.22)}
.foot-text{position:absolute;top:3369px;font-size:10.5px;color:var(--white)}
</style>
</head>
<body>

<!-- Header -->
<div class="abs brand" style="left:106px;top:46px;"><span class="brand-dot"></span>Lantern Petals</div>
<nav class="nav">
  <a class="active" style="left:342px">Home</a>
  <a style="left:431px">About Us</a>
  <a style="left:538px">For Supermarkets <svg width="9" height="6" viewBox="0 0 9 6"><path d="M1 1l3.5 3.5L8 1" stroke="#444" fill="none" stroke-width="1.3"/></svg></a>
  <a style="left:694px">For Franchisees <svg width="9" height="6" viewBox="0 0 9 6"><path d="M1 1l3.5 3.5L8 1" stroke="#444" fill="none" stroke-width="1.3"/></svg></a>
  <a style="left:842px">Our Gallery <svg width="9" height="6" viewBox="0 0 9 6"><path d="M1 1l3.5 3.5L8 1" stroke="#444" fill="none" stroke-width="1.3"/></svg></a>
</nav>
<div class="btn" style="left:981px;top:45px;width:104px;height:30px;">Contact Us</div>

<!-- Hero -->
<div class="abs hero" role="img" aria-label="Florist workbench with tulips, twine, ribbons and scissors around kraft paper"></div>
<div class="abs hero-paper" role="img" aria-label="Sheet of kraft wrapping paper"></div>
<div class="abs eyebrow center" style="top:236px;left:317px;width:600px;">Lantern Petals</div>
<h1 class="abs serif center" style="top:280px;left:317px;width:600px;font-size:34px;line-height:46px;font-weight:400;color:var(--ink);">Fresh Flowers Convey<br>Special Sentiments</h1>
<div class="abs serif center" style="top:394px;left:317px;width:600px;font-size:13px;color:var(--ink);">love, happiness, joy - which every person deserves.</div>
<div class="btn" style="left:568px;top:434px;width:136px;height:41px;">Get Started Now!</div>

<!-- Renewal -->
<h2 class="abs serif center" style="top:641px;font-size:24px;font-weight:400;color:var(--ink);letter-spacing:.4px;">Renewal, Termination &amp; Transfer</h2>
<div class="abs serif center" style="top:680px;font-size:11px;color:var(--ink);">Terms of &nbsp;the Franchise Agreement. Conditions for Renewal and Extension</div>

<div class="card" style="left:180px;">
  <svg width="62" height="54" viewBox="0 0 62 54" fill="none" stroke="#11793d" stroke-width="2">
    <rect x="4" y="14" width="36" height="26" rx="2"/><path d="M40 22h10l8 9v9H40"/><circle cx="14" cy="44" r="5"/><circle cx="48" cy="44" r="5"/><path d="M16 14c-4-8 6-10 6 0c0-10 10-8 6 0"/>
    <text x="9" y="32" font-family="Poppins,sans-serif" font-size="10" font-weight="600" fill="#11793d" stroke="none">FREE</text>
  </svg>
  <h3>FREE SHIPPING</h3>
  <p>There are many variations of passages of Lorem Ipsum available, but the majority have</p>
</div>
<div class="card" style="left:468px;">
  <svg width="56" height="54" viewBox="0 0 56 54" fill="none" stroke="#11793d" stroke-width="2">
    <path d="M50 27a23 23 0 1 1-8-17"/><path d="M42 4v7h-7"/>
    <text x="9" y="33" font-family="Poppins,sans-serif" font-size="15" font-weight="600" fill="#11793d" stroke="none">24/7</text>
  </svg>
  <h3>SUPPORT 24/7</h3>
  <p>There are many variations of passages of Lorem Ipsum available, but the majority have</p>
</div>
<div class="card" style="left:759px;">
  <svg width="60" height="58" viewBox="0 0 60 58" fill="none" stroke="#11793d" stroke-width="2">
    <rect x="4" y="2" width="44" height="40"/><path d="M18 2v14l5-4 5 4V2"/><circle cx="46" cy="44" r="12" fill="#fff"/><path d="M41 50l10-12"/><circle cx="41" cy="39" r="2"/><circle cx="51" cy="49" r="2"/>
  </svg>
  <h3>ORDER DISCOUNT</h3>
  <p>There are many variations of passages of Lorem Ipsum available, but the majority have</p>
</div>
<div class="btn" style="left:568px;top:965px;width:136px;height:42px;">Receiving Benefits</div>

<!-- About -->
<div class="abs" style="left:0;top:1118px;width:640px;height:477px;background:var(--panel);"></div>
<div class="photo" style="left:640px;top:1118px;width:560px;height:477px;background:
  radial-gradient(ellipse 200px 170px at 260px 230px,#f4d2b8 0%,rgba(244,210,184,0) 100%),
  radial-gradient(ellipse 160px 140px at 140px 160px,#e6b4bd 0%,rgba(230,180,189,0) 100%),
  radial-gradient(ellipse 180px 160px at 180px 320px,#8c4a44 0%,rgba(140,74,68,0) 100%),
  radial-gradient(ellipse 200px 180px at 480px 80px,#2f3c3b 0%,rgba(47,60,59,0) 100%),
  linear-gradient(180deg,#56625a 0%,#b89a86 50%,#8a6a52 100%);" role="img" aria-label="Hand holding a lush bouquet of peonies, roses and berries"></div>
<h2 class="abs serif" style="left:164px;top:1199px;font-size:24px;font-weight:400;color:var(--ink);">About Lantern Petals</h2>
<p class="abs para" style="left:164px;top:1261px;width:370px;">Fresh flowers convey special sentiments - love, happiness, joy - which every person deserves. Lantern Petals is an entrepreneurial company created to make top quality fresh flowers and artisan-designed bouquets accessible to every consumer at affordable prices.<br>Lantern Petals brings the best of professional florists and supermarkets together for the benefit of consumers. It supports a national network of</p>
<div class="btn" style="left:164px;top:1467px;width:137px;height:42px;">Read More</div>

<!-- Supermarkets -->
<div class="abs eyebrow center" style="top:1701px;">For Supermarkets</div>
<h2 class="abs serif center" style="top:1721px;font-size:23px;font-weight:400;color:var(--ink);">Supermarket Flower Departments Benefit</h2>
<p class="abs para" style="left:258px;top:1784px;width:684px;text-align:center;">However their quality of stems and bouquets is often poor and in-store service is limited. In contrast, professional florists typically sell the finest quality stems, design the most beautiful bouquets and provide the finest customer service, but their costs and customer prices are high. Supermarkets find that Lantern Petals, through their florist franchise network, is able to improve their financial outcomes, provide attentive customer service and satisfaction, and lift the quality of the entire store environment.</p>
<svg class="abs" style="left:65px;top:1854px" width="42" height="42" viewBox="0 0 42 42"><circle cx="21" cy="21" r="21" fill="#11793d"/><path d="M27 21H15m5-5l-5 5 5 5" stroke="#fff" stroke-width="1.6" fill="none"/></svg>
<svg class="abs" style="left:1085px;top:1854px" width="42" height="42" viewBox="0 0 42 42"><circle cx="21" cy="21" r="21" fill="#e07b39"/><path d="M15 21h12m-5-5l5 5-5 5" stroke="#fff" stroke-width="1.6" fill="none"/></svg>
<div class="btn" style="left:510px;top:1915px;width:180px;height:42px;">More For Supermarkets</div>
<div class="photo" style="left:0;top:1996px;width:1200px;height:165px;background:linear-gradient(180deg,#ffffff 0%,#f6d35a 28%,#e8ac22 55%,#b98a22 80%,#8e8a34 100%);" role="img" aria-label="Row of blooming sunflowers"></div>

<!-- Gallery -->
<h2 class="abs serif center" style="top:2261px;font-size:24px;font-weight:400;color:var(--ink);">Our Gallery</h2>
<p class="abs para" style="top:2323px;left:370px;width:460px;text-align:center;">Inspirational photos highlighting store layouts, product displays, and customer experiences.</p>
<div class="photo" style="left:115px;top:2412px;width:182px;height:185px;background:radial-gradient(circle at 50% 50%,#e6a7a8 0%,#d9c2c9 55%,#e8dfd6 100%);" role="img" aria-label="Mixed pastel bouquet"></div>
<div class="photo" style="left:311px;top:2412px;width:185px;height:185px;background:radial-gradient(circle at 50% 45%,#8f93cf 0%,#c7cbe2 55%,#eef0f3 100%);" role="img" aria-label="Blue and white hydrangea bouquet"></div>
<div class="photo" style="left:509px;top:2412px;width:185px;height:185px;background:radial-gradient(circle at 50% 50%,#d2b2a4 0%,#a6928a 55%,#7f8a7e 100%);" role="img" aria-label="Roses and peonies arrangement"></div>
<div class="photo" style="left:706px;top:2412px;width:186px;height:185px;background:radial-gradient(circle at 50% 45%,#e3919f 0%,#efcfd3 50%,#f4f2ee 100%);" role="img" aria-label="Pink roses and calla lilies in a vase"></div>
<div class="photo" style="left:905px;top:2412px;width:181px;height:185px;background:radial-gradient(circle at 50% 50%,#d8b840 0%,#c2478c 45%,#3f5a2c 100%);" role="img" aria-label="Bright gerbera bouquet"></div>
<div class="btn" style="left:510px;top:2625px;width:180px;height:42px;">More Our Gallery</div>

<!-- Contact form -->
<div class="lbl" style="left:171px;top:2781px;">First Name</div>
<div class="lbl" style="left:393px;top:2781px;">Last Name</div>
<div class="field" style="left:169px;top:2798px;width:200px;height:37px;"></div>
<div class="field" style="left:390px;top:2798px;width:200px;height:37px;"></div>
<div class="lbl" style="left:171px;top:2847px;">Email Address</div>
<div class="lbl" style="left:393px;top:2847px;">Phone Number</div>
<div class="field" style="left:169px;top:2864px;width:200px;height:37px;"></div>
<div class="field" style="left:390px;top:2864px;width:200px;height:37px;"></div>
<div class="lbl" style="left:171px;top:2913px;">Message</div>
<div class="field" style="left:169px;top:2930px;width:421px;height:73px;"></div>
<div class="btn" style="left:173px;top:3027px;width:181px;height:42px;">Submit Request</div>

<!-- Contact info -->
<div class="abs eyebrow" style="left:640px;top:2784px;">Contact Us</div>
<h2 class="abs serif" style="left:640px;top:2810px;font-size:24px;font-weight:400;color:var(--ink);">Get In Touch</h2>
<p class="abs" style="left:640px;top:2847px;width:400px;font-size:11px;line-height:22px;color:var(--muted);">For more information about becoming a franchisee with us, please reach out:</p>
<div class="contact-line" style="top:2899px;"><svg width="13" height="13" viewBox="0 0 24 24"><path fill="#e07b39" d="M6.6 10.8a15 15 0 0 0 6.6 6.6l2.2-2.2c.3-.3.7-.4 1-.2 1.1.4 2.3.6 3.6.6.6 0 1 .4 1 1V20c0 .6-.4 1-1 1A17 17 0 0 1 3 4c0-.6.4-1 1-1h3.5c.6 0 1 .4 1 1 0 1.3.2 2.5.6 3.6.1.3 0 .7-.2 1z"/></svg>Phone: (555) 214-3086</div>
<div class="contact-line" style="top:2926px;"><svg width="13" height="13" viewBox="0 0 24 24"><path fill="#e07b39" d="M12 2a7 7 0 0 0-7 7c0 5 7 13 7 13s7-8 7-13a7 7 0 0 0-7-7zm0 9.5A2.5 2.5 0 1 1 12 6.5a2.5 2.5 0 0 1 0 5z"/></svg>Email: info@lantern-petals.com</div>
<div class="contact-line" style="top:2952px;line-height:15px;"><svg width="13" height="13" viewBox="0 0 24 24"><path fill="#e07b39" d="M3 5h18v14H3zM3 6l9 7 9-7" stroke="#fff" stroke-width="1.2"/></svg>Address: 48 Petal Lane, Meadow<br>Town, FL 30512</div>

<!-- Footer -->
<footer class="abs footer"></footer>
<div class="abs brand" style="left:0;width:1200px;justify-content:center;top:3236px;font-size:26px;color:var(--white);"><span class="brand-dot" style="background:var(--white);width:26px;height:26px;"></span>Lantern Petals</div>
<span class="social" style="left:530px;"></span>
<span class="social" style="left:567px;"></span>
<span class="social" style="left:604px;"></span>
<span class="social" style="left:641px;"></span>
<div class="abs" style="left:185px;top:3362px;width:843px;height:1px;background:rgba(255,255,255,.3);"></div>
<div class="foot-text" style="left:185px;">© 2024 Lantern Petals, All rights reserved</div>
<div class="foot-text" style="left:821px;">Terms &amp; conditions</div>
<div class="foot-text" style="left:958px;">Privacy policy</div>

</body>
</html>
```